Road Construction Company needs business cards

We would like a new business card designed for our business.

We're a road construction company based in Qld, Australia.

Can the business card please have the following information on it.

Name: Warren Halbeck
Position: General Manager
Phone: 0472 915 348
Email: Warren.halbeck@tovrin.com.au
Address: 87 Marrow Ave, Pendlebay, QLD, 4023
Website: www.tovrin.com.au

Visually we'd like the card to be professional and simple.

Attached is our logo.

Our website is www.tovrin.com.au

Target Market(s)

Men aged 25-60

Contact Information for Business Card

As listed in project description

Font styles to use
Serif

Requirements
Must have
• Large logo on back of card

```html
<!DOCTYPE html>
<html lang="en">
<head>
<meta charset="utf-8">
<title>Tovrin – Business Card</title>
<link rel="stylesheet" href="https://fonts.googleapis.com/css2?family=Exo+2:wght@400;500;800;900&display=swap">
<style>
  :root{
    --stage:#2d2d2d;
    --card:#000000;
    --brand-blue:#0a5ab4;
    --accent-blue:#3a9fe0;
    --text-light:#d9d9d9;
  }
  *{margin:0;padding:0;box-sizing:border-box}
  html,body{width:1200px;height:1015px;overflow:hidden;background:var(--stage)}
  body{font-family:"Exo 2",sans-serif;position:relative}
  .card{
    position:absolute;width:620px;height:354px;background:var(--card);
    box-shadow:0 14px 30px rgba(0,0,0,.55);
  }
  .card--front{left:190px;top:110px}
  .card--back{left:390px;top:530px}

  .logo{display:flex;align-items:center;gap:12px;color:var(--brand-blue);
    font-weight:900;letter-spacing:.04em;text-transform:uppercase;line-height:1}
  .logo__mark{background:var(--accent-blue);flex:none}
  .card--front .logo{position:absolute;left:50%;top:50%;transform:translate(-50%,-50%);font-size:68px}
  .card--front .logo__mark{width:22px;height:22px}
  .card--back .logo{position:absolute;right:44px;top:52px;font-size:46px}
  .card--back .logo__mark{width:15px;height:15px}

  .holder{position:absolute;left:44px;top:58px}
  .holder__name{color:var(--brand-blue);font-weight:900;font-size:22px;letter-spacing:.06em;text-transform:uppercase}
  .holder__role{color:var(--accent-blue);font-weight:500;font-size:17px;margin-top:2px}

  .rule{position:absolute;left:64px;width:44px;height:2px;background:var(--brand-blue)}
  .rule--one{top:140px}
  .rule--two{top:228px}

  .address{position:absolute;left:80px;top:160px;color:var(--text-light);font-size:16px;line-height:1.35}
  .contacts{position:absolute;left:64px;top:246px;list-style:none;color:var(--text-light);font-size:16px;line-height:1.45}
  .contacts li{display:flex;align-items:center;gap:10px}
  .contacts svg{width:15px;height:15px;flex:none}
</style>
</head>
<body>
  <section class="card card--front" aria-label="Card front">
    <div class="logo"><span class="logo__mark"></span>Tovrin</div>
  </section>

  <section class="card card--back" aria-label="Card back">
    <div class="holder">
      <p class="holder__name">Warren Halbeck</p>
      <p class="holder__role">General Manager</p>
    </div>
    <div class="logo"><span class="logo__mark"></span>Tovrin</div>

    <span class="rule rule--one"></span>
    <p class="address">87 Marrow Ave<br>Pendlebay, QLD, 4023</p>
    <span class="rule rule--two"></span>

    <ul class="contacts">
      <li>
        <svg viewBox="0 0 24 24" aria-hidden="true"><path fill="#0a5ab4" d="M6.6 10.8a15.1 15.1 0 0 0 6.6 6.6l2.2-2.2a1 1 0 0 1 1-.25 11.4 11.4 0 0 0 3.6.57 1 1 0 0 1 1 1V20a1 1 0 0 1-1 1A17 17 0 0 1 3 4a1 1 0 0 1 1-1h3.5a1 1 0 0 1 1 1c0 1.25.2 2.45.57 3.57a1 1 0 0 1-.25 1z"/></svg>
        0472 915 348
      </li>
      <li>
        <svg viewBox="0 0 24 24" aria-hidden="true"><path fill="#0a5ab4" d="M2 5h20v14H2zm2 2v.5l8 5 8-5V7z"/></svg>
        Warren.halbeck@tovrin.com.au
      </li>
      <li>
        <svg viewBox="0 0 24 24" aria-hidden="true"><g fill="none" stroke="#0a5ab4" stroke-width="2"><circle cx="12" cy="12" r="9"/><path d="M3 12h18M12 3c3 3 3 15 0 18M12 3c-3 3-3 15 0 18"/></g></svg>
        www.tovrin.com.au
      </li>
    </ul>
  </section>
</body>
</html>
```